****Business Card Design for Quarrystone Development. Design based around attached logo/company name

I’m looking for business card design for my company Quarrystone Development Group,LLC. Design should be professional, sharp and minimal. Outside of the attached logos, greyscale colors for remainder of cards. My thoughts are two-sided card with attached logo on one side and my info on the other but open to one-sided as well with right design.
Target Market(s)
Real estate professionals including banks, private investors, property owners, developers, commercial tenants like Brewlantern, Grovika or Tanquist’s.
Industry/Entity Type
Commercial real estate development and investments.
Contact Information for Business Card
Name, title, email, phone #’s, web address and physical address
Font styles to use
Other font styles liked:
- Helvetica, Garamond, etc
Colors
Designer to choose only greyscale colors for use in the design.
Requirements
Must have
- Attached logo first or second options.
Nice to have
- Two sided card with logo on one side. Attached Logo/company name can be laid out any way that flows as long as it’s legible.name
Should not have
- No loud colors. ***Please do not include logo, I have removed the company design with a logo image.

```html
<!DOCTYPE html>
<html lang="en">
<head>
<meta charset="utf-8">
<title>Quarrystone Development Group, LLC — Business Card</title>
<link rel="stylesheet" href="https://fonts.googleapis.com/css2?family=Cinzel:wght@400&family=Tinos:wght@400&display=swap">
<style>
  :root {
    --backdrop: #2a2a2b;
    --card-dark: #232426;
    --card-dark-edge: #1c1d1f;
    --card-light: #f4f4f4;
    --brand-grey: #6a6d77;
    --brand-grey-dark: #5c606c;
    --ink-light: #e6e6e6;
  }
  * { margin: 0; padding: 0; box-sizing: border-box; }
  html, body { width: 1200px; height: 1138px; overflow: hidden; }
  body {
    background: var(--backdrop);
    position: relative;
    font-family: "Tinos", "Times New Roman", serif;
  }
  .card {
    position: absolute;
    width: 622px;
    height: 374px;
    border-radius: 16px;
    overflow: hidden;
    background: linear-gradient(160deg, var(--card-dark) 0%, var(--card-dark-edge) 100%);
  }
  .card--front { left: 272px; top: 184px; }
  .card--back  { left: 274px; top: 606px; }

  .brand {
    position: absolute;
    font-family: "Cinzel", "Times New Roman", serif;
    font-weight: 400;
    line-height: 1;
    white-space: nowrap;
  }
  .brand__name { display: block; letter-spacing: 0.5px; }
  .brand__sub  { display: block; letter-spacing: 2.2px; margin-top: 6px; }

  .card--front .brand { left: 45px; top: 117px; color: var(--brand-grey); }
  .card--front .brand__name { font-size: 36px; }
  .card--front .brand__sub  { font-size: 14px; }

  .back-panel { position: absolute; inset: 0; width: 622px; height: 374px; }

  .card--back .brand {
    left: 460px; top: 140px; transform: translateX(-50%);
    text-align: center; color: var(--brand-grey-dark);
  }
  .card--back .brand__name { font-size: 33px; }
  .card--back .brand__sub  { font-size: 14px; }

  .holder { position: absolute; left: 27px; top: 94px; color: var(--ink-light); }
  .holder__name { font-size: 24px; letter-spacing: 0.6px; line-height: 1.1; }
  .holder__title { font-size: 15px; margin-top: 4px; }

  .contact { position: absolute; left: 31px; top: 262px; list-style: none; color: var(--ink-light); font-size: 15px; }
  .contact__item { display: flex; align-items: center; height: 22px; }
  .contact__icon { width: 13px; height: 13px; margin-right: 16px; fill: var(--ink-light); }
  .address { position: absolute; left: 27px; top: 326px; color: var(--ink-light); font-size: 15px; }
</style>
</head>
<body>
  <section class="card card--front" aria-label="Card front">
    <div class="brand">
      <span class="brand__name">QUARRYSTONE</span>
      <span class="brand__sub">DEVELOPMENT GROUP, LLC</span>
    </div>
  </section>

  <section class="card card--back" aria-label="Card back">
    <svg class="back-panel" viewBox="0 0 622 374" aria-hidden="true">
      <path d="M314,0 C286,70 292,220 420,262 C500,282 590,272 622,268 L622,0 Z" fill="var(--card-light)"/>
    </svg>
    <div class="brand">
      <span class="brand__name">QUARRYSTONE</span>
      <span class="brand__sub">DEVELOPMENT GROUP, LLC</span>
    </div>

    <div class="holder">
      <p class="holder__name">JOHN DOE SMITH</p>
      <p class="holder__title">Managing Director</p>
    </div>

    <ul class="contact">
      <li class="contact__item">
        <svg class="contact__icon" viewBox="0 0 16 16"><path d="M3 2h3l1.5 3.5-2 1.2a8 8 0 0 0 3.8 3.8l1.2-2L14 10v3a1 1 0 0 1-1 1A12 12 0 0 1 2 3a1 1 0 0 1 1-1z"/></svg>
        555-014-2290
      </li>
      <li class="contact__item">
        <svg class="contact__icon" viewBox="0 0 16 16"><path d="M1 3h14v10H1z M1 3l7 6 7-6" fill="none" stroke="#e6e6e6" stroke-width="1.6"/></svg>
        john@yourwebsite.com
      </li>
      <li class="contact__item">
        <svg class="contact__icon" viewBox="0 0 16 16"><circle cx="8" cy="8" r="6.5" fill="none" stroke="#e6e6e6" stroke-width="1.4"/><path d="M1.5 8h13M8 1.5c-3 3.5-3 9.5 0 13M8 1.5c3 3.5 3 9.5 0 13" fill="none" stroke="#e6e6e6" stroke-width="1.2"/></svg>
        www.yourwebsite.com
      </li>
    </ul>
    <p class="address">234 Anywhere St., Any City, Any Town, US 123456</p>
  </section>
</body>
</html>
```